redesign my website bluekeelvoyages.net and make it user friendly

I already have a website, bluekeelvoyages.net, and want a redesign in WordPress with Elementor Pro, using the same text/content. The goal is to improve:

Design quality (colors, fonts, spacing, visual flow)
User experience (easy navigation, clear offers)
Conversion readiness (calls-to-action, trust signals, booking flow)
Technical side (SEO basics, fast speed, full mobile responsiveness)

The site should look modern, clean, fun, engaging, interactive and optimized for speed and usability.

I would like the 11 page to be consolidate dto 6 as follows: Home (main landing, highlights)

Sailboat Trips (all packages, itineraries, pricing)
Boats (fleet details, features, photos)
How It Works (booking process, FAQs, travel info, what to expect)
Blog
Contact Us (form, WhatsApp, phone, etc.)

Target Market(s)

sailboat trip customers for San Blas Islands in Panama

Industry/Entity Type

Travel, Boat Tour Agency

Coding

Coded - Design and coding required

Number of Pages Required

3 page

Font styles to use
Sans Serif
Other font styles liked:
• Oswalg and sans serif

Colors
0054AA
0677BA
7BADD7
CADEEF
E8F1F8
0094D4
00A9DD
6FCCEA
C7EBF8
E9F6FB
FFC000
F8CF3A
FAE287
FDF2CF
FEFAEE
F0912C
F2A743
F7CA91
FBE8D2
FDF5EE

Requirements
Must have
• Home (main landing, highlights) Sailboat Trips (all packages, itineraries, pricing) Boats (fleet details, features, photos) How It Works (booking process, FAQs, travel info, what to expect) Blog (updates, travel tips, inspiration) Contact Us (form, WhatsApp, phone, etc.)
Nice to have
• I want it to look professionla and be very user friendy to entice people to contact me to book boat trips
Should not have
• a store

```html
<!DOCTYPE html>
<html lang="en">
<head>
<meta charset="utf-8">
<title>Blue Keel Voyages – San Blas Sailing</title>
<link rel="stylesheet" href="https://fonts.googleapis.com/css2?family=Oswald:wght@500;600;700&family=Poppins:wght@400;500;600;700&display=swap">
<style>
:root{
  --navy:#232b5c;
  --navy-deep:#1c2350;
  --orange:#f08a24;
  --orange-soft:#fbe8d2;
  --sea:#1f9bb8;
  --sea-light:#6fccea;
  --sky:#7badd7;
  --grey-bg:#f2f2f2;
  --text:#2b2b2b;
  --white:#fff;
}
*{box-sizing:border-box;margin:0;padding:0}
html,body{width:1200px;height:4598px;overflow:hidden}
body{position:relative;font-family:"Poppins",sans-serif;color:var(--text);background:var(--white)}
.abs{position:absolute}
.heading{font-family:"Oswald",sans-serif;font-weight:700;text-transform:uppercase;color:var(--navy);letter-spacing:.5px;line-height:1.1}
.btn{position:absolute;display:flex;align-items:center;justify-content:center;border-radius:30px;font-weight:600;font-size:13px;text-transform:uppercase;letter-spacing:.3px}
.btn-orange{background:var(--orange);color:var(--white);box-shadow:0 4px 10px rgba(240,138,36,.3)}
.btn-white{background:var(--white);color:var(--orange);box-shadow:0 4px 14px rgba(0,0,0,.12)}
.btn-pale{background:var(--orange-soft);color:var(--orange)}
.photo{position:absolute;overflow:hidden}

/* header */
.site-header{position:absolute;left:0;top:0;width:1200px;height:158px;background:var(--white)}
.brand{position:absolute;left:110px;top:100px;font-family:"Oswald",sans-serif;font-weight:600;font-size:21px;color:var(--navy);letter-spacing:.5px}
.brand-dot{position:absolute;left:160px;top:40px;width:44px;height:44px;border-radius:50%;background:var(--sky)}
.nav{position:absolute;top:103px;left:348px;display:flex;gap:30px;font-size:15px;font-weight:500;color:var(--navy)}
.nav .active{color:var(--orange);border-bottom:2px solid var(--orange);padding-bottom:2px}
.social-top{position:absolute;top:36px;left:730px;display:flex;gap:8px}
.social-top span{width:30px;height:30px;border-radius:50%;background:#e6e6e6}
.social-top span.on{background:var(--orange)}
.call-icon{position:absolute;left:866px;top:26px;width:54px;height:54px;border-radius:50%;background:var(--white);box-shadow:0 3px 12px rgba(0,0,0,.12);display:flex;align-items:center;justify-content:center}
.call-label{position:absolute;left:936px;top:30px;font-size:12px;font-weight:600;color:#555}
.call-number{position:absolute;left:936px;top:48px;font-size:20px;font-weight:700;color:var(--navy)}

/* hero */
.hero{position:absolute;left:0;top:158px;width:1200px;height:730px;background:linear-gradient(160deg,#2f7e8c 0%,#2fa7b3 45%,#1f7f97 100%)}
.hero-box{position:absolute;left:111px;top:129px;width:530px;height:335px;border-radius:18px;background:rgba(35,43,92,.92)}
.hero-kicker{position:absolute;left:38px;top:38px;font-family:"Oswald",sans-serif;font-size:21px;color:var(--orange);text-transform:uppercase}
.hero-title{position:absolute;left:38px;top:68px;font-family:"Oswald",sans-serif;font-weight:700;font-size:52px;color:var(--white)}
.hero-list{position:absolute;left:38px;top:148px;list-style:none;color:var(--white);font-size:21px}
.hero-list li{display:flex;align-items:center;gap:16px;height:43px}
.dots{position:absolute;left:1137px;top:255px;display:flex;flex-direction:column;gap:12px}
.dots span{width:12px;height:12px;border-radius:50%;border:1.5px solid var(--white)}
.dots span.on{background:var(--white)}

/* about */
.section-text{font-size:15px;line-height:25px;color:#333;text-align:justify}

/* tours */
.tours{position:absolute;left:0;top:1468px;width:1200px;height:764px;background:var(--grey-bg)}
.tour-card{position:absolute;top:207px;width:300px;text-align:center}
.tour-ring{width:300px;height:300px;border-radius:50%;border:5px solid var(--sea);padding:6px;background:var(--white)}
.tour-ring.orange{border-color:var(--orange)}
.tour-ring div{width:100%;height:100%;border-radius:50%}
.tour-title{margin-top:30px;font-size:17px;font-weight:700;color:var(--navy);text-transform:uppercase}
.tour-text{margin:6px auto 0;width:280px;font-size:15px;line-height:25px;color:#333}

/* fleet */
.fleet{position:absolute;left:0;top:2232px;width:1200px;height:402px;background:linear-gradient(100deg,#1e3c86 0%,#1f63a8 55%,#1b8dc4 100%)}
.boat-card{position:absolute;top:2403px;width:309px;height:492px;background:var(--white);border-radius:14px;box-shadow:0 6px 20px rgba(0,0,0,.12);text-align:center}
.boat-photo{position:absolute;left:7px;top:7px;width:295px;height:225px;border-radius:10px}
.boat-name{position:absolute;left:0;right:0;top:255px;font-size:17px;font-weight:700;color:var(--navy);text-transform:uppercase}
.boat-text{position:absolute;left:20px;right:20px;top:280px;font-size:15px;line-height:25px;color:#333}
.slider-arrow{position:absolute;width:34px;height:34px;border-radius:50%;display:flex;align-items:center;justify-content:center}

/* testimonial */
.quote-card{position:absolute;left:292px;top:3097px;width:714px;height:296px;background:var(--white);box-shadow:0 6px 24px rgba(0,0,0,.08)}
.quote-text{position:absolute;left:138px;top:30px;width:540px;font-size:17px;line-height:28px;color:#333}
.quote-name{position:absolute;left:138px;top:222px;font-size:20px;font-weight:700;color:var(--navy)}
.stars{position:absolute;left:138px;top:250px;color:var(--orange);font-size:15px;letter-spacing:2px}

/* form */
.inquiry{position:absolute;left:0;top:3520px;width:1200px;height:800px;background:var(--grey-bg)}
.field{position:absolute;height:47px;background:var(--white);border-radius:4px;box-shadow:0 2px 6px rgba(0,0,0,.05);font-size:14px;color:#333;padding:0 17px;display:flex;align-items:center;justify-content:space-between}

/* footer */
.footer{position:absolute;left:0;top:4200px;width:1200px;height:398px;background:var(--navy)}
.foot-col{position:absolute;top:105px;color:var(--white)}
.foot-col h4{font-size:17px;font-weight:700;text-transform:uppercase;margin-bottom:14px}
.foot-col ul{list-style:none}
.foot-col li{font-size:14px;height:37.5px;display:flex;align-items:center;gap:18px}
.bullet{width:12px;height:12px;border-radius:50%;border:3px solid var(--orange)}
.contact-item{display:flex;align-items:flex-start;gap:18px;font-size:14px;line-height:22px;height:50px}
.contact-icon{flex:none;width:36px;height:36px;border-radius:50%;background:var(--white);display:flex;align-items:center;justify-content:center}
.foot-line{position:absolute;left:110px;top:340px;width:980px;height:1px;background:rgba(255,255,255,.2)}
.copyright{position:absolute;left:0;width:1200px;top:364px;text-align:center;color:var(--white);font-size:13px}
.social-foot{position:absolute;left:975px;top:350px;display:flex;gap:7px}
.social-foot span{width:32px;height:32px;border-radius:50%;border:1.5px solid var(--white)}
.social-foot span.on{background:var(--orange);border-color:var(--orange)}
</style>
</head>
<body>

<header class="site-header">
  <div class="brand-dot"></div>
  <div class="brand">BLUE KEEL VOYAGES</div>
  <nav class="nav">
    <span class="active">Home</span><span>About Us</span><span>Pricing</span><span>Services</span><span>Blog</span><span>FAQs</span><span>Contact Us</span>
  </nav>
  <div class="social-top" aria-label="Social links"><span></span><span class="on"></span><span></span></div>
  <div class="call-icon">
    <svg width="26" height="26" viewBox="0 0 24 24" fill="none" stroke="#f08a24" stroke-width="2"><path d="M22 16.9v3a2 2 0 0 1-2.2 2 19.8 19.8 0 0 1-8.6-3.1 19.5 19.5 0 0 1-6-6A19.8 19.8 0 0 1 2.1 4.2 2 2 0 0 1 4.1 2h3a2 2 0 0 1 2 1.7c.1.9.4 1.8.7 2.7a2 2 0 0 1-.5 2.1L8 9.8a16 16 0 0 0 6 6l1.3-1.3a2 2 0 0 1 2.1-.5c.9.3 1.8.6 2.7.7a2 2 0 0 1 1.9 2z"/></svg>
  </div>
  <div class="call-label">CALL US:</div>
  <div class="call-number">+573005550147</div>
  <div class="btn btn-orange" style="left:955px;top:90px;width:133px;height:47px">Book Now</div>
</header>

<section class="hero">
  <div class="photo" role="img" aria-label="Aerial view of a palm island with white sand and a sailboat anchored in turquoise water" style="inset:0;background:linear-gradient(155deg,#4e8a5a 0%,#2fa2a8 30%,#33b6bd 55%,#1c7d96 100%)"></div>
  <div class="hero-box">
    <div class="hero-kicker">Welcome to</div>
    <div class="hero-title">SAN BLAS ISLANDS</div>
    <ul class="hero-list">
      <li><svg width="20" height="20" viewBox="0 0 20 20"><rect x="1" y="1" width="18" height="18" rx="2" fill="none" stroke="#1f9bb8" stroke-width="2"/><path d="M5 10l4 4 7-8" fill="none" stroke="#1f9bb8" stroke-width="2.4"/></svg>Panama Sailing Vacations.</li>
      <li><svg width="20" height="20" viewBox="0 0 20 20"><rect x="1" y="1" width="18" height="18" rx="2" fill="none" stroke="#1f9bb8" stroke-width="2"/><path d="M5 10l4 4 7-8" fill="none" stroke="#1f9bb8" stroke-width="2.4"/></svg>Ultimate Beaches &amp; Catamaran Tours</li>
    </ul>
    <div class="btn btn-orange" style="left:41px;top:246px;width:236px;height:47px">Charter Inquiry Form</div>
  </div>
  <div class="dots"><span></span><span class="on"></span><span></span><span></span></div>
  <svg class="abs" style="left:0;top:520px" width="1200" height="220" viewBox="0 0 1200 220" preserveAspectRatio="none">
    <defs><linearGradient id="heroWave" x1="0" x2="1"><stop offset="0" stop-color="#1f2a5e"/><stop offset=".55" stop-color="#2d3e7a"/><stop offset="1" stop-color="#9fb6da"/></linearGradient></defs>
    <path d="M0 130 C150 40 330 0 520 60 C700 115 820 190 1000 150 C1090 130 1150 90 1200 60 L1200 90 C1150 130 1080 190 950 200 C780 210 680 130 520 95 C340 60 170 110 0 140 Z" fill="url(#heroWave)"/>
    <path d="M0 140 C170 110 340 60 520 95 C680 130 780 210 950 200 C1080 190 1150 130 1200 90 L1200 220 L0 220 Z" fill="#fff"/>
  </svg>
</section>

<section aria-label="Who we are">
  <div class="photo" role="img" aria-label="Small palm island in calm blue water under a bright sky" style="left:111px;top:910px;width:449px;height:449px;border-radius:50%;background:linear-gradient(180deg,#6f9fd9 0%,#a7c4e8 45%,#3d8fb8 62%,#2a6f9c 100%)"></div>
  <div class="photo" role="img" aria-label="Couple on a boat deck at sunset" style="left:355px;top:1120px;width:225px;height:225px;border-radius:50%;border:7px solid #fff;background:linear-gradient(180deg,#d7a98a 0%,#e9c29c 40%,#5b6b86 70%,#cfd4dc 100%)"></div>
  <h2 class="heading abs" style="left:627px;top:935px;font-size:48px">WHO WE ARE</h2>
  <p class="section-text abs" style="left:627px;top:1010px;width:464px">We're sailors and travelers with a love for exploration. When we first arrived in San Blas, its unique beauty and culture left a lasting impression. What began as a stop along our journey soon became something more—we felt a strong connection to this place and a sincere respect for its people, traditions, and way of life.</p>
  <p class="section-text abs" style="left:627px;top:1172px;width:464px">Rather than simply making it our home, we've done our best to live in harmony with the environment and the values of the local community.</p>
  <div class="btn btn-orange" style="left:627px;top:1278px;width:228px;height:47px">Learn More About Us</div>
</section>

<section class="tours">
  <h2 class="heading abs" style="left:0;width:1200px;top:58px;text-align:center;font-size:50px">DISCOVER ULTIMATE PANAMA<br>SAILING TOURS</h2>
  <div class="tour-card" style="left:111px">
    <div class="tour-ring"><div role="img" aria-label="Catamaran anchored beside a palm island" style="background:linear-gradient(180deg,#6fa9df 0%,#9cc8e6 45%,#2ea7b8 70%,#d8e6ec 100%)"></div></div>
    <div class="tour-title">Private Charters</div>
    <p class="tour-text">Sail the beautiful islands and beaches of San Blas on a private all-inclusive catamaran.</p>
  </div>
  <div class="tour-card" style="left:450px">
    <div class="tour-ring orange"><div role="img" aria-label="Host serving drinks on deck above deep blue water with floats" style="background:linear-gradient(180deg,#2b7fc4 0%,#1e5fa8 55%,#e58aa8 75%,#f1f1f1 100%)"></div></div>
    <div class="tour-title">Shared Charters</div>
    <p class="tour-text">Share the experience with others for a more affordable alternative to a private charter.</p>
  </div>
  <div class="tour-card" style="left:789px">
    <div class="tour-ring"><div role="img" aria-label="Group of friends smiling together on a boat" style="background:linear-gradient(180deg,#8fb4d6 0%,#b78d72 45%,#6d4d3d 75%,#c6b2a2 100%)"></div></div>
    <div class="tour-title">Family Friendly Boat Trips</div>
    <p class="tour-text">San Blas is perfect for kids, with calm waters, safe snorkeling, and fun island-hopping.</p>
  </div>
  <div class="btn btn-white" style="left:188px;top:649px;width:146px;height:48px">Learn More</div>
  <div class="btn btn-orange" style="left:527px;top:649px;width:146px;height:48px">Learn More</div>
  <div class="btn btn-white" style="left:866px;top:649px;width:146px;height:48px">Learn More</div>
</section>

<section class="fleet">
  <h2 class="heading abs" style="left:0;width:1200px;top:68px;text-align:center;font-size:50px;color:#fff">FEATURED CATAMARANS</h2>
</section>
<div class="boat-card" style="left:111px">
  <div class="boat-photo" role="img" aria-label="White catamaran near a tropical beach" style="background:linear-gradient(180deg,#4f8f5e 0%,#6fc6c6 40%,#3bb4c4 70%,#e9f2f2 100%)"></div>
  <div class="boat-name">Marlin 42</div>
  <p class="boat-text">"We started as strangers and left as friends! The crew made sure everyone felt welcome, and every moment was filled with fun and laughter."</p>
  <div class="btn btn-pale" style="left:82px;top:423px;width:145px;height:45px">Info &amp; Price</div>
</div>
<div class="boat-card" style="left:445px">
  <div class="boat-photo" role="img" aria-label="Catamaran moored off a palm island" style="background:linear-gradient(180deg,#7fb3de 0%,#3f8b5a 40%,#37b3bd 65%,#6fcbd4 100%)"></div>
  <div class="boat-name">Coral 55F</div>
  <p class="boat-text">"We started as strangers and left as friends! The crew made sure everyone felt welcome, and every moment was filled with fun and laughter."</p>
  <div class="btn btn-orange" style="left:82px;top:423px;width:145px;height:45px">Info &amp; Price</div>
</div>
<div class="boat-card" style="left:780px">
  <div class="boat-photo" role="img" aria-label="Large catamaran with red deck in turquoise water" style="background:linear-gradient(180deg,#2f9fb8 0%,#3fb8c4 45%,#e6e2dc 70%,#2a9ab3 100%)"></div>
  <div class="boat-name">Coral 55S</div>
  <p class="boat-text">"We started as strangers and left as friends! The crew made sure everyone felt welcome, and every moment was filled with fun and laughter."</p>
  <div class="btn btn-pale" style="left:82px;top:423px;width:145px;height:45px">Info &amp; Price</div>
</div>
<div class="slider-arrow" style="left:39px;top:2505px;background:#fff"><svg width="14" height="14" viewBox="0 0 14 14"><path d="M9 2L4 7l5 5" fill="none" stroke="#232b5c" stroke-width="2.2"/></svg></div>
<div class="slider-arrow" style="left:1127px;top:2505px;background:var(--orange)"><svg width="14" height="14" viewBox="0 0 14 14"><path d="M5 2l5 5-5 5" fill="none" stroke="#fff" stroke-width="2.2"/></svg></div>

<section aria-label="Testimonials">
  <h2 class="heading abs" style="left:0;width:1200px;top:3003px;text-align:center;font-size:50px">WHAT THEY SAY</h2>
  <div class="quote-card">
    <p class="quote-text">Wow. We absolutely loved loved loved our time sailing through the San Blas islands. The food was absolutely amazing (highlights of lobster and octopus!) and enjoyed the daily cocktails after a day of relaxing while sailing through, snorkeling with captain Mateo and paddle boarding in paradise...</p>
    <div class="quote-name">- DANA WHITFIELD</div>
    <div class="stars">★★★★★</div>
    <svg class="abs" style="left:620px;top:220px" width="52" height="40" viewBox="0 0 52 40"><path d="M2 40V22C2 10 8 3 20 0v8c-6 2-8 6-8 12h8v20zM30 40V22C30 10 36 3 48 0v8c-6 2-8 6-8 12h8v20z" fill="#fbe2cc"/></svg>
  </div>
  <div class="photo" role="img" aria-label="Group of guests posing on a beach at sunset" style="left:193px;top:3145px;width:197px;height:197px;border-radius:50%;border:3px solid var(--orange);box-shadow:inset 0 0 0 7px #fff;background:linear-gradient(180deg,#f0b36a 0%,#c58a78 40%,#4f5d83 75%,#e1d8cf 100%)"></div>
  <svg class="abs" style="left:62px;top:3226px" width="52" height="32" viewBox="0 0 52 32"><path d="M50 16H4M18 2L4 16l14 14" fill="none" stroke="#f08a24" stroke-width="3"/></svg>
  <svg class="abs" style="left:1086px;top:3226px" width="52" height="32" viewBox="0 0 52 32"><path d="M2 16h46M34 2l14 14-14 14" fill="none" stroke="#f08a24" stroke-width="3"/></svg>
</section>

<section class="inquiry">
  <h2 class="heading abs" style="left:0;width:1200px;top:77px;text-align:center;font-size:50px">CHARTER INQUIRY FORM</h2>
  <div class="field" style="left:165px;top:175px;width:283px">Name</div>
  <div class="field" style="left:458px;top:175px;width:283px">Email</div>
  <div class="field" style="left:751px;top:175px;width:284px">whatsapp Number</div>
  <div class="field" style="left:165px;top:237px;width:283px">Number of Passengers<span>⇕</span></div>
  <div class="field" style="left:458px;top:237px;width:283px">Number of Days<span>⇕</span></div>
  <div class="field" style="left:751px;top:237px;width:284px">Date<svg width="14" height="14" viewBox="0 0 14 14"><rect x="1" y="2" width="12" height="11" rx="1" fill="none" stroke="#666" stroke-width="1.4"/><path d="M1 5h12M4 1v3M10 1v3" stroke="#666" stroke-width="1.4"/></svg></div>
  <div class="field" style="left:165px;top:298px;width:870px">What type of experience are you looking for? (Check all that apply)<svg width="10" height="6" viewBox="0 0 10 6"><path d="M0 0h10L5 6z" fill="#555"/></svg></div>
  <div class="field" style="left:165px;top:360px;width:870px;height:93px;align-items:flex-start;padding-top:14px">Message</div>
  <div class="btn btn-orange" style="left:513px;top:470px;width:174px;height:47px">Send Message</div>
</section>

<svg class="abs" style="left:0;top:4060px" width="1200" height="150" viewBox="0 0 1200 150" preserveAspectRatio="none">
  <defs><linearGradient id="footWave" x1="0" x2="1"><stop offset="0" stop-color="#232b5c"/><stop offset=".55" stop-color="#3a4d8a"/><stop offset="1" stop-color="#b7c7e2"/></linearGradient></defs>
  <path d="M0 150 L0 110 C160 20 360 0 560 50 C760 100 960 120 1200 60 L1200 150 Z" fill="url(#footWave)"/>
  <path d="M0 150 L0 130 C170 50 370 35 560 78 C770 125 980 140 1200 95 L1200 150 Z" fill="#fff"/>
  <path d="M0 150 L0 138 C170 62 370 50 560 92 C770 138 980 152 1200 108 L1200 150 Z" fill="#232b5c"/>
</svg>

<footer class="footer">
  <div class="abs" style="left:160px;top:140px;width:44px;height:44px;border-radius:50%;background:#fff"></div>
  <div class="abs" style="left:110px;top:248px;font-family:'Oswald',sans-serif;font-weight:600;font-size:24px;color:#fff;letter-spacing:.5px">BLUE KEEL VOYAGES</div>
  <div class="foot-col" style="left:417px">
    <h4>Explore</h4>
    <ul><li><span class="bullet"></span>Home</li><li><span class="bullet"></span>About Us</li><li><span class="bullet"></span>Pricing</li><li><span class="bullet"></span>Services</li><li><span class="bullet"></span>Blog</li></ul>
  </div>
  <div class="foot-col" style="left:614px">
    <h4>Quick Links</h4>
    <ul><li><span class="bullet"></span>FAQs</li><li><span class="bullet"></span>Contact Us</li><li><span class="bullet"></span>Itineraries</li><li><span class="bullet"></span>Activities</li><li><span class="bullet"></span>BOOK NOW</li></ul>
  </div>
  <div class="foot-col" style="left:843px">
    <h4>Contact Us</h4>
    <div class="contact-item"><span class="contact-icon"><svg width="14" height="18" viewBox="0 0 14 18"><path d="M7 0a7 7 0 0 0-7 7c0 5 7 11 7 11s7-6 7-11a7 7 0 0 0-7-7zm0 9.5A2.5 2.5 0 1 1 7 4.5a2.5 2.5 0 0 1 0 5z" fill="#f08a24"/></svg></span><span>Panama City, Panama<br>Guna Yala</span></div>
    <div class="contact-item" style="margin-top:2px"><span class="contact-icon"><svg width="16" height="12" viewBox="0 0 16 12"><rect width="16" height="12" rx="1.5" fill="#f08a24"/><path d="M1 1l7 5 7-5" fill="none" stroke="#fff" stroke-width="1.4"/></svg></span><span style="padding-top:6px">hello@bluekeelvoyages.net</span></div>
    <div class="contact-item"><span class="contact-icon"><svg width="15" height="15" viewBox="0 0 24 24"><path d="M22 16.9v3a2 2 0 0 1-2.2 2 19.8 19.8 0 0 1-8.6-3.1 19.5 19.5 0 0 1-6-6A19.8 19.8 0 0 1 2.1 4.2 2 2 0 0 1 4.1 2h3a2 2 0 0 1 2 1.7l.7 2.7a2 2 0 0 1-.5 2.1L8 9.8a16 16 0 0 0 6 6l1.3-1.3a2 2 0 0 1 2.1-.5l2.7.7a2 2 0 0 1 1.9 2z" fill="#f08a24"/></svg></span><span style="padding-top:6px">+507 6000-4182</span></div>
  </div>
  <div class="foot-line"></div>
  <div class="copyright">© 2025 BLUE KEEL VOYAGES &nbsp;- &nbsp;All Rights Reserved</div>
  <div class="social-foot" aria-label="Social links"><span></span><span class="on"></span><span></span></div>
</footer>

</body>
</html>
```